Real estate business card

I need a business card for my real estate company. I help clients buy and sell properties. I would like to keep the design very simple and professional. I would like the design to convey professionalism, safety and trust. I prefer no graphics but a simple logo design would be nice if that is part of what you do.
Updates

Please keep the designs simple. No high-rise buildings please. 

Project Deadline Extended
Reason: My design has not been finalized.

Target Market(s)

Age group 30-60 mostly affluent

Industry/Entity Type

Real Estate

Contact Information for Business Card

Velmont Realtors
Gregory Velmont, Broker
4815 Brindle Ave. #263, La Crescenta, CA 91206

Requirements
Nice to have
• Logo can be combination of my initials GV or just Z or a simple geometric shape? Please see "Desig Ideas" attachment. No pics of houses or shaking hands, dollar bills, $, %, etc...
Please use fonts similar to Helvetica for a clean, modern look (think Northern European design, simple, clean yet bold)

Also use font colors such as blue, grey in different shades. Use pastel colors if better.

```html
<!DOCTYPE html>
<html lang="en">
<head>
<meta charset="utf-8">
<title>Velmont Realtors – Business Card</title>
<link rel="stylesheet" href="https://fonts.googleapis.com/css2?family=Arimo:wght@400;700&display=swap">
<style>
  :root {
    --stage: #eef6fa;
    --card: #ffffff;
    --card-edge: #2b2b2b;
    --card-shadow: #d4d6d8;
    --ink-dark: #555a5e;
    --ink-mid: #6e7377;
    --ink-light: #8a8f93;
    --accent-cyan: #1ed2f4;
    --band-blue: #0a84b8;
    --band-text: #ffffff;
  }
  * { box-sizing: border-box; margin: 0; padding: 0; }
  html, body {
    width: 1200px; height: 927px; overflow: hidden;
    background: var(--stage);
    font-family: "Arimo", "Helvetica Neue", Helvetica, Arial, sans-serif;
  }
  .stage { position: relative; width: 1200px; height: 927px; }
  .card-shadow {
    position: absolute; left: 142px; top: 121px;
    width: 737px; height: 462px;
    background: var(--card-shadow); border-radius: 26px;
  }
  .card {
    position: absolute; left: 132px; top: 111px;
    width: 737px; height: 462px;
    background: var(--card);
    border: 1px solid var(--card-edge);
    border-radius: 26px; overflow: hidden;
  }
  .brand {
    position: absolute; right: 38px; top: 146px;
    display: flex; align-items: center; gap: 10px;
  }
  .brand-mark { width: 16px; height: 16px; background: var(--accent-cyan); }
  .brand-name { font-size: 27px; color: var(--ink-dark); font-weight: 400; }
  .person { position: absolute; left: 47px; top: 125px; }
  .person-name { font-size: 33px; font-weight: 400; color: var(--ink-dark); line-height: 1.1; }
  .person-title { font-size: 18px; color: var(--ink-light); line-height: 1.2; }
  .divider {
    position: absolute; left: 31px; top: 188px;
    width: 678px; height: 3px; background: var(--accent-cyan);
  }
  .contacts { position: absolute; left: 47px; top: 198px; list-style: none; }
  .contact {
    display: flex; align-items: center; gap: 9px;
    height: 28px; font-size: 16px; color: var(--ink-mid);
  }
  .contact svg { width: 17px; height: 17px; fill: none; stroke: var(--ink-mid); stroke-width: 1.4; }
  .contact svg .solid { fill: var(--ink-mid); stroke: none; }
  .address {
    position: absolute; left: 0; right: 0; top: 381px;
    text-align: center; font-size: 17px; color: var(--ink-mid);
  }
  .web-band {
    position: absolute; left: 0; right: 0; top: 406px; bottom: 0;
    background: var(--band-blue);
    display: flex; align-items: center; justify-content: center;
  }
  .web-address { font-size: 20px; color: var(--band-text); letter-spacing: 1px; }
</style>
</head>
<body>
<main class="stage">
  <div class="card-shadow" aria-hidden="true"></div>
  <article class="card">
    <div class="brand">
      <span class="brand-mark" aria-hidden="true"></span>
      <span class="brand-name">Velmont Realtors</span>
    </div>
    <header class="person">
      <h1 class="person-name">Gregory Velmont</h1>
      <p class="person-title">Managing Director</p>
    </header>
    <div class="divider" aria-hidden="true"></div>
    <ul class="contacts">
      <li class="contact">
        <svg viewBox="0 0 18 18" aria-label="Email"><rect x="1.5" y="4" width="15" height="10"/><path d="M1.5 4 L9 10 L16.5 4"/></svg>
        gregory@gvrealtors.com
      </li>
      <li class="contact">
        <svg viewBox="0 0 18 18" aria-label="Mobile"><rect x="5" y="3" width="8" height="14" rx="1"/><rect x="6.5" y="5" width="5" height="5"/><line x1="7" y1="3" x2="7" y2="0.5"/></svg>
        +000 00 000 0000
      </li>
      <li class="contact">
        <svg viewBox="0 0 18 18" aria-label="Phone"><path class="solid" d="M2 6 Q9 1 16 6 L14 8 L12 6.5 L6 6.5 L4 8 Z"/><path class="solid" d="M4 9 L14 9 L16 16 L2 16 Z"/></svg>
        +000 0 000 0000
      </li>
    </ul>
    <p class="address">Broker 4815 Brindle Ave. #263, La Crescenta, CA 91206</p>
    <footer class="web-band">
      <span class="web-address">www.gregoryvelmontrealtors.com</span>
    </footer>
  </article>
</main>
</body>
</html>
```